Accountability Project Graphics

I want to create 10 social media graphics (new Instagram size 4:5 (1080 x 1350 pixels) focusing on our Quilvo Accountability App, using any of the 3 pictures attached. Use the attached pics only, NO RANDOM STOCK PHOTOGRAPHY. For the color scheme, use the landing page colors/fonts (attached).
You can add any of the 3 photos attached but I mainly need BOLD text that includes these headlines and sub-headlines on them.
Please NOTE for all the headlines below, also add this sub-headline on each graphic:
Stay Consistent with RT in Your Pocket!
Here are the headlines:
• Stop Starting Over Every Monday
• You don't need more willpower. You need more support
• Built for women who are tired of doing this alone
• When Motivation Fades, RT Checks In
• The Support System You've Been Missing
• Support When Motivation Disappears
• What if RT Checked in Every Day?
• The Missing Piece Isn't Another Diet
• Eat the food you love. Stay accountable every day.
• One Bad Meal Doesn't Mean You Failed
women over 40 trying to lose weight

```html
<!DOCTYPE html>
<html lang="en">
<head>
<meta charset="utf-8">
<title>Quilvo Accountability – Social Graphics</title>
<link href="https://fonts.googleapis.com/css2?family=Playfair+Display:wght@700;800&family=Poppins:ital,wght@1,500&display=swap" rel="stylesheet">
<style>
  :root{
    --canvas:#e6e6e6;
    --rose:#c95a7e;
    --plum:#3f2a4b;
    --plum-deep:#33203f;
    --blush:#fcd1e0;
    --lavender:#e0c6f6;
    --white:#ffffff;
    --ink:#3a2347;
    --line:#d9567e;
  }
  *{margin:0;padding:0;box-sizing:border-box}
  html,body{width:1200px;height:2785px;overflow:hidden;background:var(--canvas)}
  .board{position:relative;width:1200px;height:2785px}
  .card{position:absolute;width:371px;height:464px;overflow:hidden}
  .col-a{left:222px}.col-b{left:603px}
  .row-1{top:197px}.row-2{top:672px}.row-3{top:1148px}.row-4{top:1622px}.row-5{top:2097px}
  .photo{position:absolute}
  .headline{font-family:"Playfair Display",serif;font-weight:700}
  .tagline{font-family:"Poppins",sans-serif;font-style:italic;font-weight:500;letter-spacing:.6px}
  .rule{height:1px;width:64px;background:currentColor;opacity:.85}

  /* side-panel cards */
  .side-panel{position:absolute;top:0;bottom:0;color:var(--white)}
  .side-panel .headline{position:absolute}
  .side-panel .rule{position:absolute;background:var(--white)}
  .side-panel .tagline{position:absolute;font-size:14px;line-height:22px}

  /* bottom-band cards */
  .band{position:absolute;left:0;right:0;bottom:0}
  .caption{position:absolute;left:0;right:0;text-align:center}
  .caption .headline{font-size:35px;line-height:43px}
  .caption .rule{margin:14px auto 0;background:var(--line)}
  .caption .tagline{font-size:14px;margin-top:16px}
  .on-light{color:var(--ink)}
  .on-dark{color:var(--white)}
  .chevron{position:absolute;left:0;top:0;width:371px;height:464px}
</style>
</head>
<body>
<main class="board">

  <!-- 1 -->
  <section class="card col-a row-1">
    <div class="photo" style="left:201px;top:0;width:170px;height:464px;background:linear-gradient(180deg,#4a3a33 0%,#2a2228 45%,#1c1a22 100%)" role="img" aria-label="Photo of coach smiling in a black lace top, standing in a lounge"></div>
    <div class="side-panel" style="left:0;width:201px;background:var(--rose)">
      <h2 class="headline" style="left:13px;top:62px;font-size:48px;line-height:51px">Stop Starting Over Every Monday</h2>
      <div class="rule" style="left:13px;top:334px"></div>
      <p class="tagline" style="left:13px;top:351px">Stay Consistent with<br>RT in Your Pocket!</p>
    </div>
  </section>

  <!-- 2 -->
  <section class="card col-b row-1">
    <div class="photo" style="left:0;top:0;width:158px;height:464px;background:linear-gradient(180deg,#efe6dc 0%,#d9c9b8 45%,#3b4a66 75%,#2b3550 100%)" role="img" aria-label="Photo of two women laughing together in denim outfits"></div>
    <div class="side-panel" style="left:158px;width:213px;background:var(--plum)">
      <h2 class="headline" style="left:18px;top:42px;font-size:37px;line-height:47.5px">You Don't Need More Willpower. You Need More Support</h2>
      <div class="rule" style="left:18px;top:384px"></div>
      <p class="tagline" style="left:18px;top:398px">Stay Consistent with<br>RT in Your Pocket!</p>
    </div>
  </section>

  <!-- 3 -->
  <section class="card col-a row-2">
    <div class="photo" style="left:187px;top:0;width:184px;height:464px;background:linear-gradient(160deg,#d7a9b4 0%,#c9577a 45%,#2a1c22 70%,#d6f2b4 100%)" role="img" aria-label="Photo of coach hugging a client, both laughing"></div>
    <div class="side-panel" style="left:0;width:187px;background:var(--plum);opacity:.97">
      <h2 class="headline" style="left:9px;top:18px;font-size:43px;line-height:50px">Built For Women Who Are Tired Of Doing This Alone</h2>
      <div class="rule" style="left:9px;top:386px"></div>
      <p class="tagline" style="left:9px;top:401px">Stay Consistent with<br>RT in Your Pocket!</p>
    </div>
  </section>

  <!-- 4 -->
  <section class="card col-b row-2" style="background:var(--blush)">
    <div class="photo" style="left:0;top:0;width:371px;height:276px;background:linear-gradient(180deg,#efe3d6 0%,#d8c6b3 40%,#3a4866 75%,#324061 100%)" role="img" aria-label="Photo of two women laughing together in denim outfits"></div>
    <div class="caption on-light" style="top:298px">
      <h2 class="headline">When Motivation<br>Fades, RT Checks In</h2>
      <div class="rule"></div>
      <p class="tagline">Stay Consistent withRT in Your Pocket!</p>
    </div>
  </section>

  <!-- 5 -->
  <section class="card col-a row-3" style="background:var(--rose)">
    <div class="photo" style="left:0;top:0;width:371px;height:276px;background:linear-gradient(180deg,#5a4a40 0%,#2c2630 50%,#1d1b24 100%)" role="img" aria-label="Photo of coach smiling in a black lace top, standing in a lounge"></div>
    <div class="caption on-dark" style="top:292px">
      <h2 class="headline">The Support System<br>You've Been Missing</h2>
      <div class="rule" style="background:var(--plum)"></div>
      <p class="tagline">Stay Consistent withRT in Your Pocket!</p>
    </div>
  </section>

  <!-- 6 -->
  <section class="card col-b row-3" style="background:var(--plum-deep)">
    <div class="photo" style="left:0;top:0;width:371px;height:276px;background:linear-gradient(160deg,#e9c9e6 0%,#c85078 45%,#2a1c22 65%,#dff3b9 100%)" role="img" aria-label="Photo of coach hugging a client, both laughing"></div>
    <div class="caption on-dark" style="top:298px">
      <h2 class="headline">Support When<br>Motivation Disappears</h2>
      <div class="rule"></div>
      <p class="tagline">Stay Consistent withRT in Your Pocket!</p>
    </div>
  </section>

  <!-- 7 -->
  <section class="card col-a row-4">
    <div class="photo" style="left:0;top:0;width:371px;height:464px;background:linear-gradient(180deg,#5a4a40 0%,#2c2630 50%,#1d1b24 100%)" role="img" aria-label="Photo of coach smiling in a black lace top, standing in a lounge"></div>
    <svg class="chevron" viewBox="0 0 371 464"><polygon points="0,299 185.5,257 371,299 371,464 0,464" fill="#3a2347"/></svg>
    <div class="caption on-dark" style="top:316px">
      <h2 class="headline">What If RT Checked<br>In Every Day?</h2>
      <div class="rule"></div>
      <p class="tagline">Stay Consistent withRT in Your Pocket!</p>
    </div>
  </section>

  <!-- 8 -->
  <section class="card col-b row-4">
    <div class="photo" style="left:0;top:0;width:371px;height:464px;background:linear-gradient(160deg,#ecc8ec 0%,#c85078 45%,#2a1c22 62%,#dff3b9 100%)" role="img" aria-label="Photo of coach hugging a client, both laughing"></div>
    <svg class="chevron" viewBox="0 0 371 464"><polygon points="0,299 185.5,257 371,299 371,464 0,464" fill="#c95a7e"/></svg>
    <div class="caption on-dark" style="top:316px">
      <h2 class="headline">The Missing Piece<br>Isn't Another Diet</h2>
      <div class="rule"></div>
      <p class="tagline">Stay Consistent withRT in Your Pocket!</p>
    </div>
  </section>

  <!-- 9 -->
  <section class="card col-a row-5">
    <div class="photo" style="left:0;top:0;width:371px;height:464px;background:linear-gradient(180deg,#efe3d6 0%,#d8c6b3 35%,#3a4866 60%,#324061 100%)" role="img" aria-label="Photo of two women laughing together in denim outfits"></div>
    <svg class="chevron" viewBox="0 0 371 464"><polygon points="0,259 185.5,219 371,259 371,464 0,464" fill="#e0c6f6"/></svg>
    <div class="caption on-light" style="top:258px">
      <h2 class="headline">Eat The Food You<br>Love. Stay Accountable<br>Every Day.</h2>
      <div class="rule"></div>
      <p class="tagline">Stay Consistent withRT in Your Pocket!</p>
    </div>
  </section>

  <!-- 10 -->
  <section class="card col-b row-5">
    <div class="photo" style="left:0;top:0;width:371px;height:464px;background:linear-gradient(160deg,#3a2347 0%,#5e2c5a 40%,#c85078 60%,#dff3b9 85%)" role="img" aria-label="Photo of coach hugging a client, both laughing"></div>
    <svg class="chevron" viewBox="0 0 371 464"><polygon points="0,297 185.5,257 371,297 371,464 0,464" fill="#fcd1e0"/></svg>
    <div class="caption on-light" style="top:307px">
      <h2 class="headline">One Bad Meal Doesn't<br>Mean You Failed</h2>
      <div class="rule"></div>
      <p class="tagline">Stay Consistent withRT in Your Pocket!</p>
    </div>
  </section>

</main>
</body>
</html>
```